Bootstrap Website for Sports Technology Company

Create Bootstrap compatible, HTML and CSS stylesheet-based design templates for typography, forms, buttons, charts, navigation and other interface components for the www.tallow-pinery.com website. All designs should be Responsive CSS and Fluid.
We are transitioning www.tallow-pinery.com from Wordpress to Bootstrap and are looking for a fresh, clean landing page with navigation to other page styles. Official Colors and font are attached. Designer may recommend button styles, menu navigation, header, footer, etc. Please incorporate the graphic elements found on the tallow-pinery.com website.
Page Styles required:
- Landing Page
- Secondary Landing Page
- Five different Page Styles
- small, medium and large buttons
Designers are encouraged to submit the landing page with navigation. We will comment quickly to help with finalizing the design for final selection.
Industry/Entity Type
It Company
Look and feel
Each slider illustrates characteristics of the customer's brand and the style your logo design should communicate.

```html
<!DOCTYPE html>
<html lang="en">
<head>
<meta charset="utf-8">
<title>Tallow Pinery – Sign Up</title>
<link href="https://fonts.googleapis.com/css2?family=Cabin:wght@400;500;600;700&display=swap" rel="stylesheet">
<style>
:root{
  --ink:#4a4a4a;
  --ink-dark:#333;
  --muted:#b4b4b4;
  --field-border:#7a7a7a;
  --hero-bg:#e6e6e6;
  --hero-light:#f3f3f3;
  --ribbon-top:#f0f0f0;
  --ribbon-bottom:#a9a9a9;
  --brand-blue:#3a62b8;
  --tweet-teal:#1aa3b5;
  --footer-bg:#c3c3c3;
  --footer-text:#fdfdfd;
  --white:#fff;
}
*{box-sizing:border-box;margin:0;padding:0}
html,body{width:1200px;height:1088px;overflow:hidden}
body{position:relative;font-family:"Cabin",sans-serif;color:var(--ink);background:var(--white)}
.abs{position:absolute}

/* header */
.site-header{left:0;top:0;width:1200px;height:111px;background:linear-gradient(#fbfbfb,#ececec);border-bottom:1px solid #cfcfcf;box-shadow:0 2px 4px rgba(0,0,0,.12);z-index:2}
.brand{left:202px;top:38px;display:flex;align-items:center;gap:10px;font-size:27px;font-weight:600;color:var(--brand-blue)}
.brand-dot{width:26px;height:26px;border-radius:50%;background:#6f6f6f}
.main-nav{left:691px;top:42px;display:flex;gap:8px}
.main-nav a{display:block;height:28px;line-height:28px;text-align:center;font-size:14.5px;letter-spacing:.5px;color:var(--ink-dark);text-decoration:none;background:linear-gradient(#fff,#ececec);border:1px solid #c8c8c8;box-shadow:0 1px 2px rgba(0,0,0,.15)}

/* hero */
.hero{left:0;top:111px;width:1200px;height:594px;background:radial-gradient(ellipse at 62% 10%,var(--hero-light),var(--hero-bg) 70%)}
.ribbon{left:198px;top:111px;width:196px;height:562px;background:linear-gradient(var(--ribbon-top),var(--ribbon-bottom));border-left:1px solid #bdbdbd;border-right:1px solid #bdbdbd;box-shadow:0 4px 6px rgba(0,0,0,.2)}
.ribbon-item{position:absolute;left:0;width:196px;text-align:center}
.ribbon-art{margin:0 auto;background:linear-gradient(#6a6a6a,#4a4a4a);border-radius:6px;opacity:.85}
.ribbon-label{font-size:18px;font-weight:600;letter-spacing:.5px;color:#454545;margin-top:6px}
.ribbon-rule{position:absolute;left:34px;width:128px;border-top:1px dotted #ececec}
.ribbon-notch{position:absolute;left:0;bottom:0}

.signup{left:520px;top:156px;width:480px}
.signup h1{font-size:32px;font-weight:500;color:var(--ink);margin-left:3px;margin-bottom:11px;text-shadow:0 1px 0 #fff}
.field-row{display:flex;gap:9px;margin-bottom:7px}
.field{flex:1;height:29px;border:1px solid var(--field-border);border-radius:4px;background:var(--white);font-family:inherit;font-size:14.5px;color:var(--muted);padding:0 17px;display:flex;align-items:center}
.fine-print{font-size:8.8px;line-height:11px;color:#555;margin:10px 16px 0 6px}
.btn-signup{position:absolute;left:320px;top:258px;width:160px;height:32px;border-radius:3px;background:linear-gradient(#6b6b6b,#1e1e1e);border:1px solid #111;color:#fff;font-family:inherit;font-size:23px;font-weight:500;text-align:center;line-height:29px}

.share-bar{left:597px;top:551px;display:flex;gap:14px}
.share{width:91px;height:27px;background:linear-gradient(#fff,#efefef);border:1px solid #d0d0d0;display:flex;align-items:center;justify-content:center;gap:7px;font-size:12px;color:#2f4f9a}
.share .sq{width:10px;height:10px;background:#8a8a8a}
.share.tweet{color:var(--tweet-teal)}
.share.email{color:#555}

.product-mark{left:400px;top:596px;width:600px;text-align:right;font-size:62px;font-weight:500;color:#6f6f6f;letter-spacing:-.5px;white-space:nowrap}

/* beta band */
.beta-art{left:200px;top:722px;width:165px;height:193px;background:linear-gradient(#f6f6f6,#ececec);border-radius:8px}
.beta-title{left:438px;top:794px;font-size:47px;font-weight:700;color:#404040;white-space:nowrap;text-shadow:0 1px 1px rgba(0,0,0,.15)}

/* footer */
.site-footer{left:0;top:930px;width:1200px;height:158px;background:linear-gradient(135deg,#cacaca,var(--footer-bg) 50%,#bdbdbd);border-top:4px solid var(--brand-blue)}
.footer-col{position:absolute;top:19px}
.footer-col h3{font-size:14px;font-weight:400;color:var(--brand-blue);margin-bottom:9px}
.footer-col ul{list-style:none;padding-left:9px}
.footer-col li{font-size:10.4px;line-height:12.5px;color:var(--footer-text);white-space:nowrap}
.copyright{position:absolute;left:201px;top:113px;font-size:8.8px;color:var(--footer-text)}
</style>
</head>
<body>

<header class="site-header abs">
  <div class="brand abs"><span class="brand-dot"></span>Tallow Pinery</div>
  <nav class="main-nav abs">
    <a href="#" style="width:91px">WORLD</a>
    <a href="#" style="width:91px">GOLF</a>
    <a href="#" style="width:112px">CLUBHOUSE</a>
  </nav>
</header>

<section class="hero abs"></section>

<aside class="ribbon abs">
  <div class="ribbon-item" style="top:14px">
    <div class="ribbon-art" role="img" aria-label="Golfer addressing the ball silhouette" style="width:60px;height:118px"></div>
    <div class="ribbon-label">COLLECT</div>
  </div>
  <div class="ribbon-rule" style="top:171px"></div>
  <div class="ribbon-item" style="top:194px">
    <div class="ribbon-art" role="img" aria-label="Three-arrow analysis symbol" style="width:82px;height:82px;border-radius:50%"></div>
    <div class="ribbon-label">ANALYZE</div>
  </div>
  <div class="ribbon-rule" style="top:326px"></div>
  <div class="ribbon-item" style="top:352px">
    <div class="ribbon-art" role="img" aria-label="Sensor device emitting signal waves" style="width:100px;height:80px;background:linear-gradient(#e9e9e9,#7a7a7a)"></div>
    <div class="ribbon-label">INSTRUCT</div>
  </div>
  <svg class="ribbon-notch" width="196" height="48" viewBox="0 0 196 48">
    <polygon points="0,48 98,0 196,48" fill="#ededed"/>
    <polyline points="0,46 98,-1 196,46" fill="none" stroke="#8d8d8d" stroke-width="2"/>
  </svg>
</aside>

<form class="signup abs">
  <h1>Sign Up</h1>
  <div class="field-row"><div class="field">First Name</div><div class="field">Last Name</div></div>
  <div class="field-row"><div class="field">Your Email</div></div>
  <div class="field-row" style="margin-top:1px"><div class="field">Re-Enter Email</div></div>
  <div class="field-row" style="margin-top:1px"><div class="field">Password</div></div>
  <p class="fine-print">Lorem ipsum dolor sit amet, consectetuer adipiscing elit, sed diam nonummy nibh euismod tincidunt ut laoreet dolore magna aliquam erat volutpat.</p>
  <div class="btn-signup">Sign Up</div>
</form>

<div class="share-bar abs">
  <div class="share"><span class="sq"></span>Share</div>
  <div class="share tweet"><span class="sq"></span>Tweet</div>
  <div class="share"><span class="sq"></span>Share</div>
  <div class="share email">
    <svg width="26" height="16" viewBox="0 0 26 16"><rect x="1" y="1" width="24" height="14" fill="none" stroke="#555" stroke-width="1.3"/><polyline points="1,1 13,10 25,1" fill="none" stroke="#555" stroke-width="1.3"/><path d="M1,15 L10,8 M16,8 L25,15" fill="none" stroke="#555" stroke-width="1.3"/></svg>
    Email
  </div>
</div>

<div class="product-mark abs">Tallow Pinery Collect</div>

<div class="beta-art abs" role="img" aria-label="Line drawing of a golfer swinging beside a golf bag with sensor signals"></div>
<h2 class="beta-title abs">Now in Private Beta!</h2>

<footer class="site-footer abs">
  <div class="footer-col" style="left:198px">
    <h3>Tallow Pinery Portal</h3>
    <ul><li>Team Portal</li><li>Tallow Pinery Exchange</li></ul>
  </div>
  <div class="footer-col" style="left:379px">
    <h3>Who We Are</h3>
    <ul><li>About us</li><li>Our Company</li><li>Product Development</li></ul>
  </div>
  <div class="footer-col" style="left:570px">
    <h3>Outreach</h3>
    <ul>
      <li>Tallow Pinery Attends Hollybrook Vantage Talks 2013</li>
      <li>Tallow Pinery Attends Ridgeline Venture Summit 2013</li>
      <li>Ready to Tee Up First of Three Product Launches</li>
      <li>Tallow Pinery Attends TechHUM Spring 2013</li>
    </ul>
  </div>
  <div class="footer-col" style="left:886px">
    <h3>Other Information</h3>
    <ul><li>Privacy Policy</li><li>Terms &amp; Conditions</li></ul>
  </div>
  <p class="copyright">© 2013 All Rights Reserved - Tallow Pinery Enterprise, LLC.</p>
</footer>

</body>
</html>
```